Airline trolley needs a new amazing design for home/business use

TASK OUTLINE
Create a new design for the trolley panels and door to transform an airlines trolley into a piece of design.

TASK DESCRIPTION
CARTIVO is a company which manufactures and customize airline trolleys for home/business use.
Our customers can choose the graphics for their trolley’s panels and can also choose the inside inserts.
This contest is about designing the outside trolleys’ panels as you can see in the attached documents.

The trolleys will be sold in stores and online and we rally want the trolley to look original, eye-catching, creative and great. We want it to appeal to busness people and people that love design objects in their homes and offices.
We are in the process of making a new website which will include the configurator and the shopping cart. Each possible customer can, with the use of the configurator, choose their own design.

DESIGN ADVICE
- The design must be elegant and easily adaptable in houses or in working environments.
- The design must be uniformed on all sides
- The trolley door opens at 180° on the left side. When the door is open at 180°, it partially overlaps over the left side panel, so the design of the INSIDE DOOR must match with the design of the LEFT SIDE PANEL.
- The surfaces that will have to be decorated are:
Side panel left
Side panel right
Back panel
Door panel inside
Door panel outside

Please check on competitors website www.flugwagen-demo.de so that you can understand the type of equipment and business and its use.
WE MUST DO MUCH BETTER.

Airline designs are appreciated

Target Market(s)

Private and business

Industry/Entity Type

Airlines

Requirements
Nice to have
• aviation related design are appreciated
Should not have
• Cannot use Photographs and images with copyrights

```html
<!DOCTYPE html>
<html lang="en">
<head>
<meta charset="utf-8">
<title>CARTIVO trolley panels – Altos</title>
<link rel="stylesheet" href="https://fonts.googleapis.com/css2?family=Jost:wght@600&display=swap">
<style>
  :root {
    --page: #ffffff;
    --trolley-body: #353b3e;
    --panel-night: #151515;
    --letter: #ffffff;
  }
  html, body {
    margin: 0;
    padding: 0;
    width: 1200px;
    height: 812px;
    overflow: hidden;
    background: var(--page);
  }
  .canvas {
    position: relative;
    width: 1200px;
    height: 812px;
  }
  .trolley-body {
    position: absolute;
    left: 139px;
    top: 153px;
    width: 1030px;
    height: 546px;
    background: var(--trolley-body);
  }
  .panel {
    position: absolute;
    top: 262px;
    height: 352px;
    overflow: hidden;
    background: var(--panel-night);
  }
  .panel.short { height: 340px; }
  .panel svg {
    position: absolute;
    inset: 0;
    width: 100%;
    height: 100%;
  }
  .brand-name {
    position: absolute;
    top: 26px;
    left: 0;
    right: 0;
    margin: 0;
    display: flex;
    flex-direction: column;
    align-items: center;
    font-family: "Jost", sans-serif;
    font-weight: 600;
    font-size: 50px;
    line-height: 52px;
    color: var(--letter);
  }
  .panel-left-1 { left: 196px; width: 140px; }
  .panel-left-2 { left: 405px; width: 139px; }
  .panel-back { left: 641px; width: 104px; }
  .panel-door-outside { left: 837px; width: 99px; }
  .panel-door-inside { left: 1009px; width: 99px; }
  .door-handle-bar {
    position: absolute;
    left: 876px;
    top: 359px;
    width: 193px;
    height: 59px;
    background: var(--trolley-body);
  }
</style>
</head>
<body>
<div class="canvas">
  <div class="trolley-body"></div>

  <div class="panel panel-left-1">
    <svg viewBox="0 0 100 100" preserveAspectRatio="none" role="img" aria-label="Speckled and cross-hatched texture beneath a dark spotlight shape">
      <defs>
        <linearGradient id="texture" x1="0" y1="0" x2="1" y2="0">
          <stop offset="0" stop-color="#7d8385"/>
          <stop offset="0.55" stop-color="#5a5f61"/>
          <stop offset="1" stop-color="#d9d9d9"/>
        </linearGradient>
      </defs>
      <rect width="100" height="100" fill="url(#texture)"/>
      <polygon points="0,0 100,0 100,32 60,80 0,32" fill="#151515"/>
    </svg>
    <p class="brand-name"><span>A</span><span>L</span><span>T</span><span>O</span><span>S</span></p>
  </div>

  <div class="panel panel-left-2">
    <svg viewBox="0 0 100 100" preserveAspectRatio="none" role="img" aria-label="Speckled and cross-hatched texture beneath a dark spotlight shape">
      <rect width="100" height="100" fill="url(#texture)"/>
      <polygon points="0,0 100,0 100,32 60,80 0,32" fill="#151515"/>
    </svg>
    <p class="brand-name"><span>A</span><span>L</span><span>T</span><span>O</span><span>S</span></p>
  </div>

  <div class="panel panel-back">
    <svg viewBox="0 0 100 100" preserveAspectRatio="none" role="img" aria-label="Speckled and cross-hatched texture beneath a dark spotlight shape">
      <rect width="100" height="100" fill="url(#texture)"/>
      <polygon points="0,0 100,0 100,32 55,80 0,32" fill="#151515"/>
    </svg>
    <p class="brand-name"><span>A</span><span>L</span><span>T</span><span>O</span><span>S</span></p>
  </div>

  <div class="panel short panel-door-outside">
    <svg viewBox="0 0 100 100" preserveAspectRatio="none" role="img" aria-label="Speckled and cross-hatched texture beneath a dark spotlight shape">
      <rect width="100" height="100" fill="url(#texture)"/>
      <polygon points="0,0 100,0 100,33 55,82 0,33" fill="#151515"/>
    </svg>
    <p class="brand-name"><span>A</span><span>L</span><span>T</span><span>O</span><span>S</span></p>
  </div>

  <div class="panel short panel-door-inside">
    <svg viewBox="0 0 100 100" preserveAspectRatio="none" role="img" aria-label="Speckled and cross-hatched texture beneath a dark spotlight shape">
      <rect width="100" height="100" fill="url(#texture)"/>
      <polygon points="0,0 100,0 100,33 55,82 0,33" fill="#151515"/>
    </svg>
    <p class="brand-name"><span>A</span><span>L</span><span>T</span><span>O</span><span>S</span></p>
  </div>

  <div class="door-handle-bar"></div>
</div>
</body>
</html>
```